birchwell hollow cattle company website

we would like a home page, an about us page, a page for sires, a page for dams, A sale page where we can list progreny for sale and a contact us. on the about us page we would like there to be a family picture. on the sires page we would like to have a picture of each sire, a description beside them and a link to their online profile at northern hereford registry. on the dam page we would like to have a picture of each dam, aswell as a description beside them aswell as a link to the northern hereford registry site. would like the website to very mobile phone friendly as expecting most traffic to be on phone. we would like the website to look and feel very mich like a farm, rustic, barbed wire and other farm feels. we would also like a frozen genetics pages where we can include pictures and descriptions of the sires and dams aswell as a price for embryos and semen. we need to website to be easy to maintain so we can update pictures and information as it changes, we would like there to be a feature so that people can sign up to be on our mailing list by giving us their mailing addess and email and full name
aswell as an area where they can send us a message to contact us.

leaving for work for 3 weeks in the canadian arctic will have limited ability to use the internet

Target Market(s)

other ranchers, farmers, cattlemen,

Industry/Entity Type

farming, agriculture, cattle

Coding

Coded - Design and coding required

Requirements
Must have
• about page, contact page, sires page, dams page, SALE page.
Nice to have
• country/farm vibe, barbed wire, wood,

```html
<!DOCTYPE html>
<html lang="en">
<head>
<meta charset="utf-8">
<title>Birchwell Hollow Cattle Company</title>
<link href="https://fonts.googleapis.com/css2?family=Alfa+Slab+One&family=Roboto+Condensed:wght@400;500;700&display=swap" rel="stylesheet">
<style>
:root{
  --brown:#8b4a1f;
  --brown-dark:#6e3a18;
  --ink:#1e1e1e;
  --paper:#ffffff;
  --cream:#f6f2ec;
  --muted:#5a5a5a;
  --line:#d8d8d8;
}
*{box-sizing:border-box;margin:0;padding:0}
html,body{width:1200px;height:4454px;overflow:hidden}
body{
  font-family:"Roboto Condensed",sans-serif;color:var(--paper);
  background:linear-gradient(180deg,#262626 0,#2d2d2d 1100px,#444 1700px,#8a8a8a 2250px,#8a8a8a 2550px,#3a3a3a 3000px,#2a2a2a 3500px,#4a4a4a 3750px,#3a3a3a 4100px,#1e1e1e 4140px);
  position:relative;
}
.abs{position:absolute}
.slab{font-family:"Alfa Slab One",serif;text-transform:uppercase;letter-spacing:1px;font-weight:400}
.btn{position:absolute;display:flex;align-items:center;gap:8px;justify-content:center;background:var(--brown);color:#fff;font-weight:500;text-transform:uppercase;font-size:16px;height:38px;padding:0 14px;text-decoration:none}
.btn svg{width:12px;height:12px}
.btn.ghost{background:transparent;border:1px solid #fff}
.photo{position:absolute}

/* nav */
.nav{position:absolute;top:0;left:0;width:1200px;height:62px;background:#fff}
.nav a{position:absolute;top:24px;font-size:12.5px;font-weight:700;color:var(--ink);text-transform:uppercase;text-decoration:none}
.nav a.active{color:var(--brown)}
.nav .btn{top:16px;left:917px;height:36px;width:158px;font-size:12.5px;padding:0}
.logo-disc{position:absolute;left:551px;top:0;width:98px;height:88px;border-radius:0 0 49px 49px;background:#fff;display:flex;flex-direction:column;align-items:center;justify-content:center;color:var(--ink)}
.logo-name{font-weight:700;font-size:12px;text-transform:uppercase;text-align:center;line-height:1.15}

/* hero */
.hero-title{top:166px;width:1200px;text-align:center;font-size:58px;letter-spacing:3px}
.hero-sub{top:248px;width:1200px;text-align:center;font-size:24px}

/* about */
.about-h{left:674px;top:748px;font-size:46px;line-height:56px}
.body-p{font-size:15px;line-height:25.5px;color:#e4e4e4}
.seal{position:absolute;left:505px;top:873px;width:155px;height:155px;border-radius:50%;background:#fff;border:6px solid #2a2a2a;display:flex;align-items:center;justify-content:center}
.seal span{width:90px;height:90px;border-radius:50%;background:#1f1f1f;color:#fff;font-size:9px;font-weight:700;text-align:center;display:flex;align-items:center;justify-content:center;line-height:1.4}

.center-h{position:absolute;width:1200px;text-align:center;font-size:44px;line-height:56px}

/* category cards */
.cat-label{position:absolute;height:30px;background:#fff;color:var(--ink);font-weight:700;font-size:19px;text-transform:uppercase;display:flex;align-items:center;justify-content:space-between;padding:0 12px}
.cat-label svg{width:12px;height:12px}
.dams-panel{position:absolute;left:461px;top:1493px;width:278px;height:170px;background:var(--cream);color:var(--ink);padding:20px 14px}
.dams-panel h3{font-size:20px;font-weight:700;text-transform:uppercase}
.dams-panel p{font-size:11.5px;line-height:16px;color:var(--muted);margin-top:8px}

/* sale */
.sale{position:absolute;left:124px;top:1741px;width:950px;height:325px;background:#2f2f2f}
.sale h2{position:absolute;left:52px;top:62px;font-size:44px;line-height:56px}
.sale .divider{position:absolute;left:488px;top:60px;width:1px;height:170px;background:#777}
.sale p{position:absolute;left:540px;top:60px;width:320px}
.sale .foot{position:absolute;left:0;top:290px;width:950px;display:flex;align-items:center;gap:18px;padding:0 30px;color:#9a9a9a;font-size:16px;text-transform:uppercase}
.sale .foot i{flex:1;height:1px;background:#666}

/* why */
.why-card{position:absolute;top:2198px;width:300px;height:212px;background:#fff;color:var(--ink);text-align:center;padding:28px 14px 0}
.why-card svg{width:56px;height:56px}
.why-card h3{font-size:17px;font-weight:700;text-transform:uppercase;margin-top:16px}
.why-card p{font-size:11.5px;line-height:17px;color:var(--muted);margin-top:10px}

/* testimonials */
.testi{position:absolute;top:2604px;width:296px;height:276px;background:#fff;color:var(--ink);padding:22px 14px}
.avatar{width:48px;height:48px;border-radius:50%;background:#c9b8a6}
.testi h3{font-size:19px;font-weight:700;margin-top:16px}
.testi p{font-size:11.5px;line-height:17px;color:var(--muted);margin-top:8px}
.stars{color:var(--brown);font-size:11px;letter-spacing:2px;margin-top:8px}
.testi .by{font-size:12px;font-weight:700;text-transform:uppercase;margin-top:8px}
.trust-chip{position:absolute;left:154px;top:2830px;width:270px;height:42px;background:rgba(20,20,20,.82);display:flex;align-items:center;gap:10px;padding:0 12px;font-size:12px;line-height:15px}
.trust-chip .dots{display:flex}
.trust-chip .dots i{width:24px;height:24px;border-radius:50%;background:#c9b8a6;border:2px solid #fff;margin-right:-6px}
.pager{position:absolute;top:2913px;left:576px;display:flex;gap:10px}
.pager i{width:9px;height:9px;border-radius:50%;background:#ccc}
.pager i.on{background:var(--brown)}

/* insights */
.post-feature-text{position:absolute;left:143px;top:3446px;width:350px}
.date{font-size:12px;color:#ddd}
.post-title{font-size:18px;font-weight:700;margin-top:6px}
.post-desc{font-size:12.5px;line-height:17px;color:#ddd;margin-top:6px}
.post-item{position:absolute;left:697px;width:340px}

/* contact */
.band{position:absolute;left:124px;top:3743px;width:950px;height:355px;background:linear-gradient(180deg,#8b4a1f,#7a3f19)}
.band h2{position:absolute;left:44px;top:106px;font-size:44px}
.band p{position:absolute;left:44px;top:170px;width:460px;font-size:15px;line-height:24px;color:#f2e6dc}
.form{position:absolute;left:645px;top:3684px;width:411px;height:376px;background:#fff;padding:38px 16px 0;color:var(--ink)}
.form h2{font-size:38px;text-align:center;color:var(--ink)}
.field{position:absolute;height:32px;border:1px solid var(--line);font-size:10px;color:#999;padding:9px 12px}
.check{position:absolute;left:16px;top:275px;display:flex;align-items:center;gap:8px;font-size:12px}
.check i{width:14px;height:14px;border:1px solid #aaa}
.form .btn{left:16px;top:310px;width:379px;height:40px;font-size:17px}

/* footer */
.footer{position:absolute;left:0;top:4140px;width:1200px;height:314px;background:#1e1e1e}
.foot-col-h{font-size:20px;font-weight:500}
.foot-links{font-size:11.5px;line-height:20px;color:#ddd;list-style:none;margin-top:14px}
.vline{position:absolute;width:1px;height:205px;background:#444;top:4158px}
.contact-row{display:flex;align-items:center;gap:10px;font-size:11.5px;color:#ddd;margin-top:14px}
.contact-row span.ic{width:20px;height:20px;border-radius:50%;border:1px solid #ddd;display:flex;align-items:center;justify-content:center}
.contact-row svg{width:11px;height:11px}
.copy{position:absolute;top:4424px;width:1200px;text-align:center;font-size:11px;color:#ddd}
</style>
</head>
<body>

<!-- navigation -->
<header class="nav">
  <a class="active" style="left:155px">Home</a>
  <a style="left:202px">About Our Ranch</a>
  <a style="left:320px">Sires</a>
  <a style="left:374px">Dams</a>
  <a style="left:422px">Cattle for Sale</a>
  <a style="left:685px">Frozen Genetics</a>
  <a style="left:792px">Contact Us</a>
  <a class="btn">View Cattle for Sale <svg viewBox="0 0 12 12"><path d="M1 6h9M6.5 2.5 10 6l-3.5 3.5" stroke="#fff" stroke-width="1.5" fill="none"/></svg></a>
  <div class="logo-disc">
    <span class="logo-name">Birchwell<br>Hollow</span>
  </div>
</header>

<!-- hero -->
<div class="photo" role="img" aria-label="Black and white photo of two young cattle in a grassy pasture" style="left:0;top:62px;width:1200px;height:664px;background:linear-gradient(180deg,#2b2b2b 0,#3b3b3b 45%,#4a4a4a 75%,#333 100%)"></div>
<h1 class="abs slab hero-title">Birchwell Hollow Cattle</h1>
<p class="abs hero-sub">Registered Angus Cattle • Proven Genetics • Built on the Land</p>
<a class="btn" style="left:454px;top:305px;height:40px">View Sires <svg viewBox="0 0 12 12"><path d="M1 6h9M6.5 2.5 10 6l-3.5 3.5" stroke="#fff" stroke-width="1.5" fill="none"/></svg></a>
<a class="btn ghost" style="left:583px;top:305px;height:40px">Cattle for Sale <svg viewBox="0 0 12 12"><path d="M1 6h9M6.5 2.5 10 6l-3.5 3.5" stroke="#fff" stroke-width="1.5" fill="none"/></svg></a>

<!-- about -->
<div class="photo" role="img" aria-label="Family photo of the ranch owners and their children in front of a weathered wooden barn" style="left:124px;top:735px;width:443px;height:438px;background:linear-gradient(160deg,#7a5a42,#5a3f2c 55%,#3f3a34)"></div>
<div class="seal"><span>Sound genetics.<br>Performance.<br>Longevity.</span></div>
<h2 class="abs slab about-h">Built on the<br>land. Proven<br>in the herd.</h2>
<p class="abs body-p" style="left:674px;top:930px;width:400px">At Birchwell Hollow, we raise registered Angus cattle with a focus on sound genetics, performance, and longevity. Our breeding decisions are made with real-world ranch conditions in mind-prioritizing structural soundness, fertility, and cattle that hold up year after year. We are committed to consistency you can count on, from pasture to production.</p>
<a class="btn" style="left:674px;top:1108px">About Birchwell Hollow <svg viewBox="0 0 12 12"><path d="M1 6h9M6.5 2.5 10 6l-3.5 3.5" stroke="#fff" stroke-width="1.5" fill="none"/></svg></a>

<!-- categories -->
<h2 class="slab center-h" style="top:1246px">Built for performance.<br>Selected for consistency.</h2>
<div class="photo" role="img" aria-label="Black and white photo of a rancher tending a bull" style="left:124px;top:1383px;width:308px;height:291px;background:linear-gradient(160deg,#9a9a9a,#4a4a4a)"></div>
<div class="cat-label" style="left:140px;top:1640px;width:278px">Sires <svg viewBox="0 0 12 12"><path d="M1 6h9M6.5 2.5 10 6l-3.5 3.5" stroke="#1e1e1e" stroke-width="1.5" fill="none"/></svg></div>
<div class="photo" role="img" aria-label="Photo of cows and calves at a creek" style="left:446px;top:1383px;width:308px;height:291px;background:linear-gradient(180deg,#7f9a6a,#9a6a45 50%,#6f7f65)"></div>
<div class="dams-panel">
  <h3>Dams</h3>
  <p>Our dams are the foundation of the herd-chosen for fertility, maternal strength, and longevity. They are developed to raise calves that perform year after year.</p>
  <a class="btn" style="left:14px;top:116px;height:36px">View Dams <svg viewBox="0 0 12 12"><path d="M1 6h9M6.5 2.5 10 6l-3.5 3.5" stroke="#fff" stroke-width="1.5" fill="none"/></svg></a>
</div>
<div class="photo" role="img" aria-label="Black and white photo of a technician examining genetics beside a cow" style="left:766px;top:1383px;width:308px;height:291px;background:linear-gradient(160deg,#d8d8d8,#8a8a8a)"></div>
<div class="cat-label" style="left:782px;top:1640px;width:278px">Frozen Genetics <svg viewBox="0 0 12 12"><path d="M1 6h9M6.5 2.5 10 6l-3.5 3.5" stroke="#1e1e1e" stroke-width="1.5" fill="none"/></svg></div>

<!-- sale -->
<section class="sale">
  <h2 class="slab">Cattle ready<br>for the next<br>pasture</h2>
  <i class="divider"></i>
  <p class="body-p">Current progeny and Birchwell Hollow genetics are available for purchase, developed under real-world ranch conditions and selected for sound structure, fertility, and dependable performance. Listings are updated regularly as offerings change.</p>
  <a class="btn" style="left:540px;top:200px">View Sale <svg viewBox="0 0 12 12"><path d="M1 6h9M6.5 2.5 10 6l-3.5 3.5" stroke="#fff" stroke-width="1.5" fill="none"/></svg></a>
  <div class="foot"><i></i>Birchwell Hollow Cattle<i></i></div>
</section>

<!-- why -->
<h2 class="slab center-h" style="top:2118px">Why Birchwell Hollow</h2>
<div class="why-card" style="left:126px">
  <svg viewBox="0 0 56 56" role="img" aria-label="Cattle icon"><circle cx="28" cy="28" r="18" fill="none" stroke="#8b4a1f" stroke-width="2.5"/></svg>
  <h3>Registered Angus Program</h3>
  <p>Our herd is built on a fully registered Angus program, ensuring documented pedigrees, verified lineage, and consistency you can trust when making breeding and purchasing decisions.</p>
</div>
<div class="why-card" style="left:450px">
  <svg viewBox="0 0 56 56" fill="none" stroke="#8b4a1f" stroke-width="2.5"><path d="M14 48C30 36 26 20 42 8M14 8c4 18 24 22 28 40"/><path d="M19 16h14M17 26h22M19 38h16"/></svg>
  <h3>Transparent, Traceable Genetics</h3>
  <p>Every sire and dam in our program is clearly documented, allowing buyers to review pedigrees, performance data, and breeding history with confidence and clarity.</p>
</div>
<div class="why-card" style="left:774px">
  <svg viewBox="0 0 56 56" role="img" aria-label="Cattle pair icon"><circle cx="20" cy="28" r="13" fill="none" stroke="#8b4a1f" stroke-width="2.5"/><circle cx="36" cy="28" r="13" fill="none" stroke="#8b4a1f" stroke-width="2.5"/></svg>
  <h3>Performance-Focused Breeding</h3>
  <p>We select and develop cattle with real-world performance in mind-prioritizing fertility, structural soundness, disposition, and longevity over short-term trends.</p>
</div>

<!-- testimonials -->
<h2 class="slab center-h" style="top:2463px">Trusted by cattlemen who<br>value consistency</h2>
<div class="photo" role="img" aria-label="Photo of a smiling cattleman crouching beside cattle at a fence" style="left:124px;top:2604px;width:296px;height:276px;background:linear-gradient(160deg,#6c7a58,#4f4a3c 60%,#2e2e2a)"></div>
<div class="trust-chip"><span class="dots"><i></i><i></i><i></i></span><span style="margin-left:10px">Trusted by 1,000+ People<br>Birchwell Hollow Cattle</span></div>
<div class="testi" style="left:469px">
  <div class="avatar" role="img" aria-label="Reviewer portrait"></div>
  <h3>“Consistent, Easy-Keeping Cattle”</h3>
  <p>“The Birchwell Hollow cattle have been easy-keeping, sound, and consistent. They’ve held up under real working conditions and performed the way good Angus cattle should. We’ve been pleased with their structure, disposition, and overall durability in our program.”</p>
  <div class="stars">★★★★★</div>
  <div class="by">– Commercial Angus Producer, Alberta</div>
</div>
<div class="testi" style="left:778px">
  <div class="avatar" role="img" aria-label="Reviewer portrait"></div>
  <h3>“Clear Pedigrees. Honest Information.”</h3>
  <p>“We appreciate the transparency behind their genetics. Pedigrees are clear, information is easy to access, and the cattle perform the way they’re described. That level of clarity makes it easier to evaluate genetics and make confident breeding decisions.”</p>
  <div class="stars">★★★★★</div>
  <div class="by">– Seedstock Producer</div>
</div>
<div class="pager"><i></i><i class="on"></i><i></i></div>

<!-- insights -->
<h2 class="slab center-h" style="top:2979px">Practical insights<br>from the ranch</h2>
<div class="photo" role="img" aria-label="Photo of a rancher couple standing beside a black cow" style="left:124px;top:3112px;width:388px;height:438px;background:linear-gradient(170deg,#6a6a58,#4a4238 60%,#2a2520)"></div>
<div class="post-feature-text">
  <div class="date">February 12, 2026</div>
  <div class="post-title">Selecting Sires for Real-World Performance</div>
  <div class="post-desc">How we evaluate sires beyond the numbers, and what traits translate best to working ranch conditions.</div>
</div>

<div class="photo" role="img" aria-label="Photo of a cow herd grazing in a green pasture" style="left:531px;top:3112px;width:146px;height:113px;background:linear-gradient(180deg,#8aa86a,#6a8a4e)"></div>
<div class="post-item" style="top:3122px">
  <div class="date">March 3, 2026</div>
  <div class="post-title">Building a Consistent Angus Cow Herd</div>
  <div class="post-desc">What we look for in fertility, structure, and maternal strength-and why consistency matters more than trends.</div>
</div>
<div class="photo" role="img" aria-label="Photo of a black cow in a green handling chute" style="left:531px;top:3263px;width:146px;height:112px;background:linear-gradient(160deg,#3f6a4a,#1f2a24)"></div>
<div class="post-item" style="top:3275px">
  <div class="date">January 21, 2026</div>
  <div class="post-title">Why Registered Genetics Matter</div>
  <div class="post-desc">Understanding pedigree documentation, performance records, and long-term value in registered Angus cattle.</div>
</div>
<div class="photo" role="img" aria-label="Photo of cattle in a barn pen" style="left:531px;top:3416px;width:146px;height:113px;background:linear-gradient(160deg,#8a6a50,#2a2522)"></div>
<div class="post-item" style="top:3428px">
  <div class="date">December 18, 2025</div>
  <div class="post-title">Managing Cattle for Longevity</div>
  <div class="post-desc">Management practices we use to develop cattle that stay productive and sound year after year.</div>
</div>
<a class="btn" style="left:516px;top:3582px;height:40px">View All Insigts <svg viewBox="0 0 12 12"><path d="M1 6h9M6.5 2.5 10 6l-3.5 3.5" stroke="#fff" stroke-width="1.5" fill="none"/></svg></a>

<!-- contact -->
<div class="photo" role="img" aria-label="Faded photo of cattle grazing in a field" style="left:0;top:3640px;width:1200px;height:500px;background:linear-gradient(180deg,rgba(90,90,90,.5),rgba(40,40,40,.7))"></div>
<section class="band">
  <h2 class="slab">Stay connected</h2>
  <p>Get updates on cattle for sale, genetics availability, and news from the ranch-delivered directly to you with clear, timely information to help you plan purchases and stay connected to the Birchwell Hollow program.</p>
</section>
<form class="form">
  <h2 class="slab">Get in touch</h2>
  <div class="field" style="left:16px;top:104px;width:187px">First Name*</div>
  <div class="field" style="left:208px;top:104px;width:187px">Last Name*</div>
  <div class="field" style="left:16px;top:142px;width:187px">Email*</div>
  <div class="field" style="left:208px;top:142px;width:187px">Phone No*</div>
  <div class="field" style="left:16px;top:180px;width:379px;height:82px">Message*</div>
  <div class="check"><i></i>I have read the privacy policy</div>
  <a class="btn">Submit <svg viewBox="0 0 12 12"><path d="M1 6h9M6.5 2.5 10 6l-3.5 3.5" stroke="#fff" stroke-width="1.5" fill="none"/></svg></a>
</form>

<!-- footer -->
<footer class="footer">
  <div class="abs" style="left:124px;top:55px;font-weight:700;font-size:17px;text-transform:uppercase;line-height:20px">Birchwell Hollow<br><span style="font-size:10px;letter-spacing:3px">Cattle Company</span></div>
  <p class="abs" style="left:124px;top:110px;width:340px;font-size:14.5px;line-height:23px;color:#ddd">Birchwell Hollow is a registered Angus ranch focused on sound genetics, performance, and longevity. Our program is built for real-world ranch conditions and consistent results you can rely on.</p>
  <span class="abs" style="left:124px;top:234px;width:20px;height:20px;border:1px solid #ddd;border-radius:50%"></span>
  <div class="abs" style="left:580px;top:20px">
    <div class="foot-col-h">Main Links</div>
    <ul class="foot-links"><li>Home</li><li>About Our Ranch</li><li>Sires</li><li>Dams</li><li>Cattle for Sale</li><li>Frozen Genetics</li><li>Contact Us</li></ul>
  </div>
  <div class="abs" style="left:798px;top:20px">
    <div class="foot-col-h">Contact Us</div>
    <div class="contact-row"><span class="ic"><svg viewBox="0 0 12 12"><rect x="1" y="2.5" width="10" height="7" fill="none" stroke="#ddd"/><path d="M1 2.5 6 7l5-4.5" fill="none" stroke="#ddd"/></svg></span>info@birchwellhollow.com</div>
    <div class="contact-row"><span class="ic"><svg viewBox="0 0 12 12"><path d="M2.5 1.5 5 4 4 5.5c.7 1.3 1.2 1.8 2.5 2.5L8 7l2.5 2.5L9 11C5 10 2 7 1 3z" fill="#ddd"/></svg></span>250-555-0142 / 250-555-0187</div>
    <div class="contact-row"><span class="ic"><svg viewBox="0 0 12 12"><circle cx="6" cy="6" r="4.5" fill="none" stroke="#ddd"/><path d="M1.5 6h9M6 1.5c-2 3-2 6 0 9M6 1.5c2 3 2 6 0 9" fill="none" stroke="#ddd"/></svg></span>www.birchwellhollow.com</div>
  </div>
</footer>
<i class="vline" style="left:517px"></i>
<i class="vline" style="left:748px"></i>
<p class="copy">© 2026 Birchwell Hollow. All Rights Reserved.</p>

</body>
</html>
```